Stationary Set Rebrand for Brennick

We are a Canadian Distribution and Service Company that was established in 1969. Over the past 5 decades we have expanded our business and have warehouses across Canada. We specialize in adhesive tapes, adhesives, films, safety, warehouse, shipping, janitorial and packaging supplies.

We have updated our logo design and would like a new corporate branding identity that includes a new fresh Stationary Set (Business Cards, Letterhead, Letterhead MS Word, Envelope, Presentation Folders, Email Signatures, Notepad Covers, etc.)

Target Market(s)

Industrial Business Sector

Font styles to use
Sans Serif

Colors
0054AA
0677BA
7BADD7
CADEEF
E8F1F8
0094D4
00A9DD
6FCCEA
C7EBF8
E9F6FB
00AB8E
00BBA5
67D7C9
C6EFE9
E9F9F6
EB3D1F
EC4F4E
F09395
F8D3D4
FCEDEE

Requirements
Should not have
• Colors not too light, darker colours preferred

```html
<!DOCTYPE html>
<html lang="en">
<head>
<meta charset="utf-8">
<title>Brennick Business Card</title>
<link rel="stylesheet" href="https://fonts.googleapis.com/css2?family=Nunito:wght@400;600;800&display=swap">
<style>
  :root {
    --backdrop: #9c9c9c;
    --card: #1a1a1a;
    --card-back: #141414;
    --edge: #c4121b;
    --accent: #e0313a;
    --ink: #f2f2f2;
    --ink-soft: #d9d9d9;
    --mark-muted: #3a3a3a;
  }
  * { box-sizing: border-box; margin: 0; padding: 0; }
  html, body {
    width: 1200px; height: 1083px; overflow: hidden;
    background: var(--backdrop);
    font-family: "Nunito", sans-serif;
  }
  .stage { position: relative; width: 1200px; height: 1083px; }
  .card {
    position: absolute; left: 250px; width: 700px; height: 400px;
    background: var(--card);
    border-bottom: 5px solid var(--edge);
    border-left: 2px solid var(--edge);
    color: var(--ink);
  }
  .card--front { top: 70px; }
  .card--back { top: 560px; background: var(--card-back); }

  .brand { position: absolute; text-align: center; }
  .brand__row { display: flex; align-items: center; justify-content: center; gap: 12px; }
  .brand__name { font-weight: 800; font-size: 64px; line-height: 1; letter-spacing: 1px; color: var(--ink); }
  .brand__dot { width: 16px; height: 16px; border-radius: 50%; background: var(--accent); }
  .brand__tagline { font-weight: 600; font-size: 15px; color: var(--ink); margin-top: 6px; letter-spacing: .5px; }

  .card--front .brand { left: 250px; top: 58px; width: 380px; }
  .card--back .brand { left: 0; right: 0; top: 110px; }
  .card--back .brand__name, .card--back .brand__tagline { color: var(--mark-muted); }

  .rule { position: absolute; left: 82px; right: 52px; top: 218px; height: 2px; background: var(--accent); }

  .person { position: absolute; left: 330px; top: 150px; width: 320px; text-align: center; }
  .person__name { color: var(--accent); font-size: 25px; font-weight: 600; letter-spacing: 1px; text-transform: uppercase; line-height: 1.1; }
  .person__role { color: var(--ink-soft); font-size: 17px; margin-top: 2px; }

  .contact { position: absolute; left: 60px; top: 236px; list-style: none; font-size: 17px; line-height: 1.45; }
  .contact li { display: flex; align-items: center; gap: 10px; }
  .contact svg { width: 14px; height: 14px; fill: var(--accent); flex: none; }

  .address { position: absolute; right: 52px; bottom: 34px; text-align: right; font-size: 17px; line-height: 1.35; }

  .established { position: absolute; left: 0; right: 0; bottom: 70px; text-align: center; font-size: 18px; color: var(--ink); }
</style>
</head>
<body>
<main class="stage">
  <section class="card card--front">
    <div class="brand">
      <div class="brand__row"><span class="brand__name">Brennick</span><span class="brand__dot"></span></div>
      <p class="brand__tagline">Tape and Packaging Specialists</p>
    </div>
    <div class="person">
      <p class="person__name">Daniel Harwood</p>
      <p class="person__role">Development Manager Officer</p>
    </div>
    <div class="rule"></div>
    <ul class="contact">
      <li><svg viewBox="0 0 24 24" aria-hidden="true"><path d="M6.6 10.8a15 15 0 0 0 6.6 6.6l2.2-2.2a1 1 0 0 1 1-.25 11.4 11.4 0 0 0 3.6.57 1 1 0 0 1 1 1V20a1 1 0 0 1-1 1A17 17 0 0 1 3 4a1 1 0 0 1 1-1h3.5a1 1 0 0 1 1 1c0 1.25.2 2.45.57 3.57a1 1 0 0 1-.25 1z"/></svg>555-014-2286</li>
      <li><svg viewBox="0 0 24 24" aria-hidden="true"><path d="M2 5h20v14H2zM2 5l10 8 10-8v2l-10 8L2 7z"/></svg>daniel.harwood@brennicksupply.com</li>
      <li><svg viewBox="0 0 24 24" aria-hidden="true"><path d="M12 2a10 10 0 1 0 0 20 10 10 0 0 0 0-20zm0 2c.9 1.2 1.6 2.6 2 4h-4c.4-1.4 1.1-2.8 2-4zM4.3 14a8 8 0 0 1 0-4h3.4a16 16 0 0 0 0 4zm.8 2h3c.3 1.3.8 2.5 1.4 3.6A8 8 0 0 1 5.1 16zm3-8h-3a8 8 0 0 1 4.4-3.6C8.9 5.5 8.4 6.7 8.1 8zM12 20c-.9-1.2-1.6-2.6-2-4h4c-.4 1.4-1.1 2.8-2 4zm2.3-6H9.7a14 14 0 0 1 0-4h4.6a14 14 0 0 1 0 4zm.2 5.6c.6-1.1 1.1-2.3 1.4-3.6h3a8 8 0 0 1-4.4 3.6zm1.8-5.6a16 16 0 0 0 0-4h3.4a8 8 0 0 1 0 4z"/></svg>brennicksupply.com</li>
    </ul>
    <address class="address">412 Harbour Lane<br>Suite 210, Mississauga<br>ON L5B 3C7</address>
  </section>

  <section class="card card--back">
    <div class="brand">
      <div class="brand__row"><span class="brand__name">Brennick</span><span class="brand__dot"></span></div>
      <p class="brand__tagline">Tape and Packaging Specialists</p>
    </div>
    <p class="established">Estd. 1969</p>
  </section>
</main>
</body>
</html>
```